Garlic Farm for Farm Sales/Restaurant sales

Need a professional, but appealing to agriculture world. We are selling 27 kinds of Organic Garlic from a farm in Simla,CO. I have uploaded logo and business information-we are going to need a template, because I will need to use it for four separate people.
-We are trying to appeal to Farm to table restaurants
-As well as growers/farmers

Target Market(s)

Agriculture Sales/Restaurants-Organic

Industry/Entity Type

Agriculture

Contact Information for Business Card

Want it to look more unique then your average kelto stock card- I want it to look amazing

Font styles to use
Sans Serif

Colors
0455a3
ec1f27
fbed22
ffffff

Requirements
Must have
• Just be creative
Nice to have
• Colorful
Should not have
• plain

```html
<!DOCTYPE html>
<html lang="en">
<head>
<meta charset="utf-8">
<title>Ridgeline Garlic Co — Business Card</title>
<link href="https://fonts.googleapis.com/css2?family=Montserrat:wght@400;500;600;700&display=swap" rel="stylesheet">
<style>
  :root {
    --navy: #0b2f6b;
    --navy-deep: #082554;
    --blue: #0455a3;
    --red: #ec1f27;
    --yellow: #fbed22;
    --white: #ffffff;
    --stage: #eceae6;
    --ink: #1d2f55;
  }
  * { margin: 0; padding: 0; box-sizing: border-box; }
  html, body {
    width: 1200px; height: 950px; overflow: hidden;
    background: var(--stage);
    font-family: "Montserrat", sans-serif;
  }
  .sheet {
    width: 1200px; height: 950px;
    display: flex; flex-direction: column;
    align-items: center; justify-content: center; gap: 44px;
  }
  .card {
    position: relative;
    width: 600px; height: 343px;
    border-radius: 18px; overflow: hidden;
    box-shadow: 0 10px 26px rgba(0,0,0,.18);
  }
  .card-front { background: var(--white); }
  .card-front .swoosh { position: absolute; inset: 0; }

  .brand {
    position: absolute; left: 52px; top: 150px;
    display: flex; align-items: center; gap: 14px;
  }
  .brand-dot {
    width: 46px; height: 46px; border-radius: 50%;
    background: var(--red);
  }
  .brand-name {
    font-weight: 700; font-size: 26px; color: var(--navy);
    line-height: 1; letter-spacing: .3px;
  }

  .person {
    position: absolute; left: 52px; top: 40px;
  }
  .person-name { font-size: 22px; font-weight: 600; color: var(--navy); }
  .person-role { font-size: 13px; font-weight: 600; color: var(--red); margin-top: 4px; letter-spacing: .5px; }

  .contact {
    position: absolute; right: 30px; top: 92px;
    list-style: none; text-align: right;
    color: var(--white); font-size: 13px; font-weight: 500; line-height: 1.75;
  }
  .contact li { display: flex; justify-content: flex-end; align-items: center; gap: 8px; }
  .contact .icon { width: 14px; height: 14px; flex: none; }

  .card-back {
    background: var(--navy);
    display: flex; align-items: center; justify-content: center;
  }
  .back-mark {
    position: absolute; width: 250px; height: 250px; border-radius: 50%;
    background: rgba(255,255,255,.07);
  }
  .back-name {
    position: relative;
    font-weight: 700; font-size: 40px; color: var(--white); letter-spacing: .5px;
  }
</style>
</head>
<body>
<main class="sheet">

  <section class="card card-front" aria-label="Business card front">
    <svg class="swoosh" viewBox="0 0 600 343" preserveAspectRatio="none" aria-hidden="true">
      <path d="M318 0 C 280 110, 260 230, 150 343" fill="none" stroke="var(--red)" stroke-width="10"/>
      <path d="M352 0 C 322 90, 300 170, 270 230" fill="none" stroke="var(--yellow)" stroke-width="11"/>
      <path d="M375 0 C 335 120, 320 240, 205 343 L 600 343 L 600 0 Z" fill="var(--navy-deep)"/>
      <path d="M395 0 C 355 120, 345 240, 232 343 L 600 343 L 600 0 Z" fill="var(--white)"/>
      <path d="M405 0 C 365 120, 355 240, 244 343 L 600 343 L 600 0 Z" fill="var(--navy)"/>
    </svg>

    <div class="person">
      <p class="person-name">Dana Hollis</p>
      <p class="person-role">CEO/Founder</p>
    </div>

    <div class="brand">
      <span class="brand-dot"></span>
      <span class="brand-name">Ridgeline<br>Garlic Co</span>
    </div>

    <ul class="contact">
      <li>P.O. Box 48</li>
      <li>Bramford, CO 80999
        <svg class="icon" viewBox="0 0 14 14"><circle cx="7" cy="7" r="7" fill="var(--yellow)"/><path d="M7 3.2a2.4 2.4 0 0 0-2.4 2.4C4.6 7.6 7 10.8 7 10.8s2.4-3.2 2.4-5.2A2.4 2.4 0 0 0 7 3.2z" fill="var(--navy)"/></svg>
      </li>
      <li>555-014-2290
        <svg class="icon" viewBox="0 0 14 14"><circle cx="7" cy="7" r="7" fill="var(--yellow)"/><path d="M4.6 3.6l1.4-.3.8 1.9-.9.7a5 5 0 0 0 2.2 2.2l.7-.9 1.9.8-.3 1.4c-3.4.3-6.1-2.4-5.8-5.8z" fill="var(--navy)"/></svg>
      </li>
      <li>dana@ridgelinegarlic.com
        <svg class="icon" viewBox="0 0 14 14"><circle cx="7" cy="7" r="7" fill="var(--yellow)"/><rect x="3.5" y="4.5" width="7" height="5" fill="var(--navy)"/><path d="M3.6 4.7L7 7.3l3.4-2.6" fill="none" stroke="var(--yellow)" stroke-width=".8"/></svg>
      </li>
      <li>www.ridgelinegarlic.com
        <svg class="icon" viewBox="0 0 14 14"><circle cx="7" cy="7" r="7" fill="var(--yellow)"/><circle cx="7" cy="7" r="3.6" fill="none" stroke="var(--navy)" stroke-width=".9"/><path d="M3.4 7h7.2M7 3.4c-1.6 2-1.6 5.2 0 7.2M7 3.4c1.6 2 1.6 5.2 0 7.2" fill="none" stroke="var(--navy)" stroke-width=".8"/></svg>
      </li>
    </ul>
  </section>

  <section class="card card-back" aria-label="Business card back">
    <span class="back-mark"></span>
    <p class="back-name">Ridgeline Garlic Co</p>
  </section>

</main>
</body>
</html>
```